Northfield Builders Guild Business card

We are looking for a new business card design with photo included.
Our business is a nonprofit construction contractor membership organization. We offer business education, assist with business setup and licensing, provide safety training, and provide a member directory.
URL: www.builderslinkguild.org
Color code:
CMYK: 0 cyan, 42 magenta, 100 yellow, 0 black for Print.
Hexidecimal: #FF9900
RGB: R 255; G 153; B 0

```html
<!DOCTYPE html>
<html lang="en">
<head>
<meta charset="utf-8">
<title>Northfield Builders Guild – Business Card</title>
<link rel="stylesheet" href="https://fonts.googleapis.com/css2?family=Open+Sans:ital,wght@0,400;0,700;0,800;1,400&display=swap">
<style>
  :root {
    --bg: #1a1a1a;
    --card: #202020;
    --orange: #ff9900;
    --white: #ffffff;
    --text: #e9e9e9;
    --muted: #5a5a5a;
  }
  html, body {
    margin: 0;
    width: 1200px;
    height: 900px;
    overflow: hidden;
    background: var(--bg);
    font-family: "Open Sans", Arial, sans-serif;
  }
  .stage {
    position: relative;
    width: 1200px;
    height: 900px;
  }
  .card {
    position: absolute;
    left: 320px;
    width: 560px;
    height: 320px;
    background: var(--card);
    border-bottom: 6px solid var(--orange);
    box-sizing: border-box;
    box-shadow: 0 10px 30px rgba(0,0,0,.5);
  }
  .card--front { top: 100px; }
  .card--back  { top: 480px; }

  .brand {
    position: absolute;
    left: 40px;
    top: 92px;
    width: 210px;
    margin: 0;
    font-weight: 800;
    font-size: 30px;
    line-height: 1.05;
    text-transform: uppercase;
    color: var(--white);
    letter-spacing: .5px;
  }
  .divider {
    position: absolute;
    left: 270px;
    top: 60px;
    width: 1px;
    height: 190px;
    background: var(--orange);
  }
  .contact {
    position: absolute;
    left: 292px;
    top: 66px;
    color: var(--text);
    font-size: 13.5px;
    line-height: 1.5;
  }
  .contact__name {
    margin: 0;
    color: var(--orange);
    font-weight: 700;
    font-size: 19px;
    text-transform: uppercase;
    line-height: 1.2;
  }
  .contact__role {
    margin: 0 0 8px;
    font-style: italic;
    font-size: 14px;
  }
  .contact__address { margin: 0 0 8px; font-style: normal; }
  .contact__list { list-style: none; margin: 0; padding: 0; }
  .contact__list li { display: flex; align-items: center; gap: 7px; }
  .contact__list svg { width: 12px; height: 12px; flex: none; }

  .back-brand {
    position: absolute;
    left: 0; right: 0;
    top: 130px;
    margin: 0;
    text-align: center;
    font-weight: 800;
    font-size: 30px;
    text-transform: uppercase;
    color: var(--muted);
    letter-spacing: .5px;
  }
</style>
</head>
<body>
<main class="stage">
  <section class="card card--front" aria-label="Business card front">
    <h1 class="brand">Northfield Builders Guild</h1>
    <div class="divider"></div>
    <div class="contact">
      <p class="contact__name">Dana Whitcombe</p>
      <p class="contact__role">President</p>
      <address class="contact__address">2450 Meridian Ave., Suite #210<br>Cedar Falls, OR 97031</address>
      <ul class="contact__list">
        <li>
          <svg viewBox="0 0 24 24" aria-hidden="true"><path fill="#ff9900" d="M6.6 10.8a15 15 0 0 0 6.6 6.6l2.2-2.2c.3-.3.7-.4 1-.2 1.1.4 2.3.6 3.6.6.6 0 1 .4 1 1V20c0 .6-.4 1-1 1A17 17 0 0 1 3 4c0-.6.4-1 1-1h3.5c.6 0 1 .4 1 1 0 1.3.2 2.5.6 3.6.1.3 0 .7-.2 1z"/></svg>
          (555) 318-0476
        </li>
        <li>
          <svg viewBox="0 0 24 24" aria-hidden="true"><rect x="2" y="5" width="20" height="14" rx="1" fill="#ff9900"/><path d="M3 6l9 7 9-7" fill="none" stroke="#202020" stroke-width="2"/></svg>
          help@nbguild.org
        </li>
        <li>
          <svg viewBox="0 0 24 24" aria-hidden="true"><circle cx="12" cy="12" r="10" fill="none" stroke="#ff9900" stroke-width="2.5"/><path d="M2 12h20M12 2c3 3 3 17 0 20M12 2c-3 3-3 17 0 20" fill="none" stroke="#ff9900" stroke-width="2"/></svg>
          www.builderslinkguild.org
        </li>
      </ul>
    </div>
  </section>

  <section class="card card--back" aria-label="Business card back">
    <p class="back-brand">Northfield Builders Guild</p>
  </section>
</main>
</body>
</html>
```